I am a business consultant/coach and I am branding myself 'The Zero Fee Venture Mentor'. My business name is Bright Harbor Planning.I want an oversized postcard designed for lead generation. It will be sent through the post so will require area for an address and stamp The details that I want on the card are attached plus a photo of myself. Also I have attached a copy of my business card so that you are able to see the style and colors I use. I would like the main headline to be bold red, or bold red background Hope this is enough info.
Target Market(s)
Owners/managers of medium sized businesses
Industry/Entity Type
Business Consultant
Requirements
Must have
- The cards I want to be noticed and professional in appearance, they will be use dfor lead generation and sent through the postal service
Nice to have
- The colors that I use on my business cards are green, grey and white. I want the main headline to be in red or red backgroun dso that it stands out
Should not have
- The words that I have used are basically off my landing page for consistency

```html
<!DOCTYPE html>
<html lang="en">
<head>
<meta charset="utf-8">
<title>Bright Harbor Planning – Postcard</title>
<link href="https://fonts.googleapis.com/css2?family=Oswald:wght@300;400;500&family=Source+Sans+3:wght@400;600;700&display=swap" rel="stylesheet">
<style>
  :root{
    --bg:#e9e7e4;
    --white:#ffffff;
    --panel:#c9cacc;
    --stripe:#4a4c4f;
    --red:#e0262a;
    --green:#2a9a3a;
    --ink:#222324;
    --mark:#4b4d50;
    --back-bg:#efeeef;
    --back-panel:#e0e0e1;
  }
  *{margin:0;padding:0;box-sizing:border-box}
  html,body{width:1200px;height:1000px;overflow:hidden;background:var(--bg)}
  .stage{position:relative;width:1200px;height:1000px}
  .card{position:absolute;box-shadow:0 2px 8px rgba(0,0,0,.18);overflow:hidden}
  .card--front{left:33px;top:29px;width:607px;height:469px;background:var(--white)}
  .card--back{left:557px;top:505px;width:606px;height:469px;background:var(--back-bg)}
  .abs{position:absolute}
  .shapes{position:absolute;left:0;top:0}
  .oswald{font-family:'Oswald',sans-serif}
  .sans{font-family:'Source Sans 3',sans-serif}

  .photo{left:0;top:0;width:300px;height:372px;
    background:linear-gradient(160deg,#8fa3b3 0%,#6f8595 35%,#b8c2c8 60%,#d9dde2 100%)}

  .name{left:282px;top:30px;width:296px;text-align:center;color:var(--white);
    font-family:'Oswald',sans-serif;font-weight:400;font-size:40px;line-height:48px}
  .role{left:282px;top:84px;width:296px;text-align:center;color:var(--white);
    font-family:'Source Sans 3',sans-serif;font-size:18px;line-height:22px}
  .pitch{left:300px;top:127px;width:285px;text-align:center;color:var(--ink);
    font-family:'Oswald',sans-serif;font-weight:300;font-size:21px;line-height:26.5px}
  .divider{left:320px;top:219px;width:242px;border-top:1px dashed #555}
  .cta{left:300px;top:232px;width:285px;text-align:center;font-family:'Oswald',sans-serif}
  .cta__start{color:var(--green);font-size:25px;line-height:30px;text-decoration:underline;text-underline-offset:3px}
  .cta__turn{color:var(--ink);font-weight:300;font-size:21px;line-height:28px}
  .cta__offer{color:var(--red);font-weight:500;font-size:19px;line-height:24px}

  .contact{left:27px;top:382px;font-family:'Oswald',sans-serif;font-weight:300;font-size:14px;color:var(--ink)}
  .contact__row{display:flex;align-items:center;gap:6px;height:22px}
  .contact__row svg{flex:none}
  .contact__gap{width:12px}

  .wordmark{font-family:'Source Sans 3',sans-serif;font-weight:700;color:var(--mark);letter-spacing:-1px;white-space:nowrap}
  .front-mark{left:322px;top:352px;width:260px;text-align:center;font-size:40px;line-height:48px}
  .front-tag{left:322px;top:426px;width:260px;text-align:center;font-family:'Source Sans 3',sans-serif;font-size:19px;color:var(--ink)}

  .back-white{left:0;top:0;width:455px;height:150px;background:var(--white)}
  .back-intro{left:14px;top:28px;width:220px;text-align:center;font-family:'Oswald',sans-serif;font-weight:300;font-size:16px;line-height:22.5px;color:var(--ink)}
  .back-intro .red{color:var(--red);font-weight:400;font-size:19px}
  .back-rule{left:232px;top:32px;height:106px;border-left:1px dashed #444}
  .back-mark{left:254px;top:24px;font-size:29px;line-height:36px}
  .back-tag{left:254px;top:74px;font-family:'Source Sans 3',sans-serif;font-size:16px;color:var(--ink)}
  .back-contact{left:260px;top:106px;font-family:'Oswald',sans-serif;font-weight:300;font-size:12px;color:var(--ink)}
  .back-contact .contact__row{height:18px}

  .offer{left:0;top:152px;width:293px;height:233px;background:var(--back-panel)}
  .offer__head{height:30px;background:var(--red);color:var(--white);text-align:center;
    font-family:'Oswald',sans-serif;font-size:22px;line-height:30px}
  .offer__title{margin-top:10px;text-align:center;color:var(--green);font-family:'Oswald',sans-serif;font-size:22px;line-height:28px}
  .offer__quote{margin:8px auto 0;width:240px;text-align:center;color:var(--ink);font-family:'Oswald',sans-serif;font-weight:300;font-size:14px;line-height:19.5px}
  .offer__visit{margin-top:18px;text-align:center;color:var(--ink);font-family:'Oswald',sans-serif;font-weight:300;font-size:18px;line-height:20px}
  .offer__url{text-align:center;color:var(--green);font-family:'Oswald',sans-serif;font-size:21px;line-height:26px}
  .back-strip{left:0;top:385px;width:75px;height:84px;background:var(--back-panel)}
</style>
</head>
<body>
<div class="stage">

  <!-- Front -->
  <section class="card card--front">
    <div class="abs photo" role="img" aria-label="Portrait photo of the coach, smiling, in a white shirt outdoors"></div>
    <svg class="shapes" width="607" height="469" viewBox="0 0 607 469">
      <polygon points="295,0 607,0 607,332 312,348" fill="var(--panel)"/>
      <polygon points="278,0 297,0 314,348 298,350" fill="var(--stripe)"/>
      <polygon points="282,24 578,24 568,114 292,114" fill="var(--red)"/>
      <polygon points="0,356 607,319 607,336 0,364" fill="var(--green)"/>
      <polygon points="0,364 607,336 607,469 0,469" fill="var(--white)"/>
    </svg>

    <div class="abs name">Daniel Whitmore</div>
    <div class="abs role">Business Coach Exit Strategist</div>
    <div class="abs pitch">Future Proof Your Business<br>More Money, Time, Freedom<br>No Worries</div>
    <div class="abs divider"></div>
    <div class="abs cta">
      <div class="cta__start">START NOW</div>
      <div class="cta__turn">Turn Card Over For My</div>
      <div class="cta__offer">SPECIAL OFFER</div>
    </div>

    <div class="abs contact">
      <div class="contact__row">
        <svg width="14" height="12" viewBox="0 0 14 12"><path d="M7 0 L14 6 H12 V12 H8.5 V8 H5.5 V12 H2 V6 H0 Z" fill="var(--green)"/></svg>
        Seabrook Point, NSW, Australia
      </div>
      <div class="contact__row">
        <svg width="13" height="13" viewBox="0 0 13 13"><circle cx="6.5" cy="6.5" r="5.6" fill="none" stroke="var(--green)" stroke-width="1.3"/><path d="M4.3 3.6 L5.6 3.4 L6.1 5 L5.3 5.6 Q5.9 7.2 7.4 7.8 L8 7 L9.5 7.5 L9.3 8.8 Q6 9.2 4.3 3.6 Z" fill="var(--green)"/></svg>
        0400 555 123
        <span class="contact__gap"></span>
        <svg width="15" height="11" viewBox="0 0 15 11"><rect x="0.7" y="0.7" width="13.6" height="9.6" fill="none" stroke="var(--green)" stroke-width="1.3"/><path d="M0.7 0.7 L7.5 6 L14.3 0.7" fill="none" stroke="var(--green)" stroke-width="1.3"/></svg>
        dan@brightharbor.com.au
      </div>
      <div class="contact__row">
        <svg width="13" height="13" viewBox="0 0 13 13"><circle cx="6.5" cy="6.5" r="5.6" fill="none" stroke="var(--green)" stroke-width="1.2"/><ellipse cx="6.5" cy="6.5" rx="2.4" ry="5.6" fill="none" stroke="var(--green)" stroke-width="1"/><path d="M1 6.5 H12" stroke="var(--green)" stroke-width="1"/></svg>
        brightharbor.com.au
      </div>
    </div>

    <div class="abs wordmark front-mark">brightharbor</div>
    <div class="abs front-tag">Bright Harbor Planning</div>
  </section>

  <!-- Back -->
  <section class="card card--back">
    <div class="abs back-white"></div>
    <div class="abs back-intro">
      Commited to your Success<br>
      Any questions? Contact Me<br>
      <span class="red">Daniel Whitmore</span><br>
      Bright Harbor Planning<br>
      0400555123
    </div>
    <div class="abs back-rule"></div>
    <div class="abs wordmark back-mark">brightharbor</div>
    <div class="abs back-tag">Bright Harbor Planning</div>
    <div class="abs back-contact">
      <div class="contact__row">
        <svg width="12" height="10" viewBox="0 0 14 12"><path d="M7 0 L14 6 H12 V12 H8.5 V8 H5.5 V12 H2 V6 H0 Z" fill="var(--green)"/></svg>
        Seabrook Point, NSW, Australia
      </div>
      <div class="contact__row">
        <svg width="13" height="10" viewBox="0 0 15 11"><rect x="0.7" y="0.7" width="13.6" height="9.6" fill="none" stroke="var(--green)" stroke-width="1.3"/><path d="M0.7 0.7 L7.5 6 L14.3 0.7" fill="none" stroke="var(--green)" stroke-width="1.3"/></svg>
        dan@brightharbor.com.au
      </div>
    </div>

    <div class="abs offer">
      <div class="offer__head">ZERO FEE VENTURE MENTOR</div>
      <div class="offer__title">Special Offer - My Guatantee</div>
      <div class="offer__quote">“If I cannot uncover at least 5 times my fee from potential profits hidden within your business after one interview then it is free”</div>
      <div class="offer__visit">visit us at</div>
      <div class="offer__url">brightharbor.com.au/zerofee</div>
    </div>
    <div class="abs back-strip"></div>
  </section>

</div>
</body>
</html>
```